Brell Stone Company Business Cards

Front and Back Business Card - logo and text setup - cool design. I need workable photoshop or illustrator files so I can setup each employee card with design that is created
Updates

Hi everyone, thank you for the great entries. Please no more white and blue cards - there are so many already - black and silver only now please. thanks!

Target Market(s)

Construction Industry - Facility Managers

Industry/Entity Type

Construction

Contact Information for Business Card

I really like contemporary simplistic looks - clean neat....not opposed to seeing some black backrounds

Requirements
Must have
• Logo/website address with design on front only - www.brellstone-example.com (logo attached)
• Back:
• Name/Title/Company Address/Phone/email address
Nice to have
• Cool design
Should not have
• Nothing gimmicky like Fire or Water - since we are a Fire Protection company - it has all been done

```html
<!DOCTYPE html>
<html lang="en">
<head>
<meta charset="utf-8">
<title>Brell Stone Company – Business Cards</title>
<link rel="stylesheet" href="https://fonts.googleapis.com/css2?family=Lato:wght@400;700&family=Oswald:wght@500&display=swap">
<style>
  :root {
    --stage: #17181b;
    --card: #262729;
    --card-edge: #2d2e31;
    --silver: #c9cacc;
    --text-light: #e6e6e6;
    --rule: #8a8b8e;
    --accent-blue: #34457f;
  }
  * { box-sizing: border-box; margin: 0; padding: 0; }
  html, body { width: 1200px; height: 912px; overflow: hidden; }
  body {
    background: var(--stage);
    font-family: "Lato", sans-serif;
    position: relative;
  }
  .card {
    position: absolute;
    width: 560px;
    height: 320px;
    background: linear-gradient(160deg, var(--card-edge), var(--card));
    box-shadow: 0 18px 40px rgba(0,0,0,0.55);
    overflow: hidden;
  }
  /* Front */
  .card--front { left: 90px; top: 80px; }
  .front__brand {
    position: absolute;
    left: 0; right: 0; top: 110px;
    display: flex; align-items: center; justify-content: center; gap: 14px;
  }
  .front__brand-mark {
    width: 22px; height: 22px;
    background: var(--silver);
  }
  .front__brand-name {
    font-family: "Lato", sans-serif;
    font-weight: 700;
    font-size: 56px;
    letter-spacing: -1px;
    color: var(--silver);
    line-height: 1;
  }
  .front__web {
    position: absolute;
    left: 0; right: 0; top: 232px;
    text-align: center;
    font-size: 15px;
    letter-spacing: 0.5px;
    color: var(--text-light);
  }
  /* Back */
  .card--back { left: 550px; top: 500px; }
  .back__identity {
    position: absolute;
    right: 310px; top: 128px;
    text-align: right;
  }
  .back__name {
    font-family: "Oswald", sans-serif;
    font-weight: 500;
    font-size: 25px;
    letter-spacing: -0.5px;
    color: var(--accent-blue);
    text-transform: uppercase;
    line-height: 1.1;
  }
  .back__title {
    font-size: 15px;
    color: var(--text-light);
    margin-top: 2px;
  }
  .back__rule {
    position: absolute;
    left: 270px; top: 70px;
    width: 1px; height: 150px;
    background: var(--rule);
  }
  .back__contact {
    position: absolute;
    left: 292px; top: 78px;
    font-size: 13px;
    line-height: 1.35;
    color: var(--text-light);
  }
  .back__address { margin-bottom: 12px; }
  .back__line { display: flex; align-items: center; gap: 8px; }
  .back__icon { width: 11px; height: 11px; flex: none; }
  .back__band {
    position: absolute;
    left: 0; right: 0; bottom: 0;
    height: 7px;
    background: var(--accent-blue);
  }
</style>
</head>
<body>
  <section class="card card--front" aria-label="Business card front">
    <div class="front__brand">
      <span class="front__brand-mark"></span>
      <span class="front__brand-name">brellstone</span>
    </div>
    <p class="front__web">www.brellstone-example.com</p>
  </section>

  <section class="card card--back" aria-label="Business card back">
    <div class="back__identity">
      <p class="back__name">Dana Marlow Pierce</p>
      <p class="back__title">President</p>
    </div>
    <div class="back__rule"></div>
    <div class="back__contact">
      <p class="back__address">48 Harbor Park Lane<br>Millbrook, NY 12545</p>
      <p class="back__line">
        <svg class="back__icon" viewBox="0 0 12 12" aria-hidden="true"><path d="M2.5 1 L4.5 1 L5.2 3.5 L4 4.6 Q5 7 7.4 8 L8.5 6.8 L11 7.5 L11 9.5 Q11 11 9.5 11 Q1 10.5 1 2.5 Q1 1 2.5 1Z" fill="#34457f"/></svg>
        (555) 014-2297
      </p>
      <p class="back__line">
        <svg class="back__icon" viewBox="0 0 12 12" aria-hidden="true"><rect x="0.5" y="2.5" width="11" height="7.5" fill="#34457f"/><path d="M0.5 2.5 L6 7 L11.5 2.5" fill="none" stroke="#262729" stroke-width="1"/></svg>
        info@brellstone-example.com
      </p>
      <p class="back__line">
        <svg class="back__icon" viewBox="0 0 12 12" aria-hidden="true"><circle cx="6" cy="6" r="5.2" fill="#34457f"/><path d="M0.8 6 H11.2 M6 0.8 V11.2 M6 0.8 Q2.5 6 6 11.2 M6 0.8 Q9.5 6 6 11.2" fill="none" stroke="#262729" stroke-width="0.8"/></svg>
        www.brellstone-example.com
      </p>
    </div>
    <div class="back__band"></div>
  </section>
</body>
</html>
```